Website Design for Stratonimbus As a Service

We are building a service to allow customers to own their own private clouds easily and cheaply. Owning your own private cloud saves costs, and offers more flexibility than a public cloud provider but has historically been a complex and expensive option.

We plan to offer a service where we build and maintain your own private cloud on your own hardware for a cheap monthly costs. Similar to this service - https://nimbrovex.com/solutions/private-cloud

We already have a logo and branding in place - we'd like a website design to be tailored from this branding, see attached logo design.

Feel free to add important elements on the home page such as testimonials, client/partner logos, contact form, social media, etc using placeholder contents in addition to the document we attached.

We also plan to add sub-pages in the future so please make sure that your website design has a full navigation menu.

An example of the site we like: https://www.quorvant.com/ we'd be happy for you to take inspiration from this website.

Target Market(s)

B2B focused, we are targeting start-up/small/medium sized companies who needs help with their cloud and IT infrastructure.

Industry/Entity Type

IT

Number of Pages Required

1 page

Font styles to use
Other font styles liked:
• Please refer to the attachment - font must have Mayeka Demi Bold & Retroica

Requirements
Must have
• Please add placeholder menu since we're planning to have subpages later on.

```html
<!DOCTYPE html>
<html lang="en">
<head>
<meta charset="utf-8">
<title>Stratonimbus – Private Cloud as a Service</title>
<link rel="stylesheet" href="https://fonts.googleapis.com/css2?family=Comfortaa:wght@400;700&family=Roboto:wght@400;500;700&display=swap">
<style>
:root{
  --blue:#1f8ad6;
  --blue-dark:#1574c0;
  --blue-light:#3da3ea;
  --ink:#2b2b2b;
  --muted:#7a7a7a;
  --grey-band:#5f6163;
  --icon-grey:#6d6d6d;
  --footer:#232323;
  --line:#d9d9d9;
  --white:#ffffff;
}
*{box-sizing:border-box;margin:0;padding:0}
html,body{width:1200px;height:4190px;overflow:hidden}
body{position:relative;font-family:"Roboto",Arial,sans-serif;color:var(--ink);background:var(--white)}
.abs{position:absolute}
.display{font-family:"Comfortaa","Trebuchet MS",sans-serif}
.btn{position:absolute;display:flex;align-items:center;justify-content:center;gap:8px;border-radius:24px;font-weight:700;font-size:15px;letter-spacing:.2px}
.btn .arrow{width:14px;height:14px;border-radius:50%;display:inline-flex;align-items:center;justify-content:center}
.btn-blue{background:var(--blue);color:var(--white)}
.btn-blue .arrow{background:var(--white)}
.btn-white{background:var(--white);color:var(--blue)}
.btn-white .arrow{background:var(--blue)}
.section-mark{position:absolute;left:591px;width:18px;height:18px;border-radius:50%;background:var(--blue)}
.section-title{position:absolute;left:0;width:1200px;text-align:center;font-size:34px;color:#555}
.section-title b{color:var(--blue)}

/* header / hero */
.hero{position:absolute;left:0;top:0;width:1200px;height:740px;background:linear-gradient(180deg,#1d7fce 0%,#2790dc 60%,#3aa1e6 100%);overflow:hidden}
.brand{position:absolute;display:flex;align-items:center;gap:8px;font-family:"Comfortaa",sans-serif;font-weight:700}
.brand .dot{border-radius:50%}
.nav{position:absolute;left:386px;top:38px;display:flex;gap:23px;font-size:14.5px;font-weight:500;color:var(--white)}
.login{position:absolute;left:987px;top:31px;width:101px;height:34px;border-radius:18px;background:var(--white);color:var(--blue);font-size:14px;font-weight:500;display:flex;align-items:center;justify-content:center}
.hero-title{position:absolute;left:110px;top:158px;font-size:32px;line-height:38px;color:var(--white);font-weight:400}
.hero-title b{font-weight:700}
.hero-text{position:absolute;left:110px;top:296px;width:500px;font-size:13.5px;line-height:27px;color:#e8f3fc}
.hero-text strong{display:block;margin-top:10px;color:var(--white);font-weight:500;line-height:25px}
.hero-art{position:absolute;left:580px;top:95px;width:620px;height:640px;border-radius:40% 30% 20% 30%;background:radial-gradient(circle at 60% 40%,#a9ddfa 0%,#6cc0f1 35%,#2d8fd9 75%,rgba(45,143,217,0) 100%)}

/* benefits */
.benefit{position:absolute;width:230px}
.benefit h3{font-size:16px;font-weight:700;color:#222;margin-bottom:10px}
.benefit p{font-size:12.5px;line-height:20px;color:var(--muted)}
.benefit.left{text-align:right}
.b-icon{position:absolute;width:80px;height:80px;border-radius:50%;border:2px solid #e3e3e3;background:var(--white);display:flex;align-items:center;justify-content:center}
.b-icon span{width:62px;height:62px;border-radius:50%;display:block}
.b-icon.grey span{background:var(--icon-grey)}
.b-icon.blue span{background:var(--blue)}
.hub{position:absolute;left:488px;top:912px;width:224px;height:224px;border-radius:50%;background:var(--white);box-shadow:0 4px 22px rgba(0,0,0,.14);display:flex;align-items:center;justify-content:center}
.hub-ring{width:188px;height:188px;border-radius:50%;border:3px solid var(--blue);display:flex;align-items:center;justify-content:center}
.hub-core{width:120px;height:120px;border-radius:50%;background:var(--blue)}

/* transformation band */
.band{position:absolute;left:0;top:1288px;width:1200px;height:546px;background:linear-gradient(180deg,#5b5d5f,#6a6c6e 50%,#5b5d5f)}
.band h2{position:absolute;left:0;top:70px;width:1200px;text-align:center;color:var(--white);font-size:32px;line-height:40px;font-weight:400}
.band h2 b{font-weight:700}
.band .copy{position:absolute;left:150px;top:166px;width:900px;text-align:center;color:#f0f0f0;font-size:13.5px;line-height:24px}
.band .copy p{margin-bottom:6px}
.trait{position:absolute;top:340px;display:flex;align-items:center;gap:36px;color:var(--white);font-weight:700;font-size:16px}
.trait svg{display:block}

/* public cloud cards */
.card{position:absolute;top:2016px;width:311px;height:363px;background:var(--white);border:1px solid #ececec;border-radius:4px;text-align:center;padding:0 24px}
.card.active{box-shadow:0 8px 24px rgba(0,0,0,.09);border-bottom:4px solid var(--blue-dark)}
.card .c-icon{width:88px;height:88px;border-radius:50%;background:var(--blue);margin:38px auto 22px}
.card h3{font-size:17px;line-height:23px;font-weight:500;color:#222;margin-bottom:16px}
.card p{font-size:13px;line-height:24.5px;color:var(--muted)}

/* difference */
.diff{position:absolute;left:0;top:2582px;width:1200px;height:508px;background:linear-gradient(90deg,#1e86d2,#2792dc)}
.diff-art{position:absolute;left:44px;top:52px}
.diff h2{position:absolute;left:637px;top:100px;color:var(--white);font-size:33px;font-weight:400}
.diff h2 b{font-weight:700}
.diff ul{position:absolute;left:637px;top:158px;width:460px;list-style:none}
.diff li{position:relative;padding-left:28px;color:#eef6fd;font-size:13.5px;line-height:24px;margin-bottom:6px}
.diff li::before{content:"";position:absolute;left:2px;top:6px;width:12px;height:12px;border-radius:50%;background:var(--white)}
.diff li::after{content:"";position:absolute;left:6px;top:8px;width:3px;height:6px;border:solid var(--blue);border-width:0 2px 2px 0;transform:rotate(45deg)}

/* contact */
.contact-info{position:absolute;top:3266px;display:flex;align-items:flex-start;gap:18px}
.contact-info h4{font-size:15px;font-weight:700;color:#444;letter-spacing:.3px}
.contact-info p{font-size:13.5px;color:var(--muted);margin-top:6px}
.field{position:absolute;border:1px solid #dcdcdc;background:var(--white);border-radius:2px;font-size:13px;color:#8a8a8a;padding:0 18px;display:flex;align-items:center}
.field.area{align-items:flex-start;padding-top:22px}

/* footer */
.footer{position:absolute;left:0;top:3850px;width:1200px;height:340px;background:var(--footer);color:#e8e8e8}
.f-col{position:absolute;top:52px}
.f-col h4{font-size:15px;font-weight:700;color:var(--white);margin-bottom:18px}
.f-contact{position:relative;padding-left:24px;margin-bottom:12px;font-size:12.5px;line-height:18px}
.f-contact b{display:block;font-size:11px;font-weight:700}
.f-contact i{position:absolute;left:0;top:3px;width:11px;height:11px;border-radius:50%;background:var(--blue)}
.f-links a{display:block;font-size:13px;color:#e8e8e8;text-decoration:none;margin-bottom:9px}
.subscribe{position:absolute;left:790px;top:90px;width:296px;height:44px;border-radius:22px;background:var(--white)}
.subscribe span{position:absolute;left:22px;top:14px;font-size:11.5px;color:#777}
.subscribe em{position:absolute;right:0;top:0;width:122px;height:44px;border-radius:22px;background:var(--blue);color:var(--white);font-style:normal;font-weight:700;font-size:16px;display:flex;align-items:center;justify-content:center}
.social{position:absolute;top:207px;width:30px;height:30px;border-radius:50%;border:1.5px solid #cfcfcf}
.legal{position:absolute;top:295px;font-size:12.5px;color:#e8e8e8}
</style>
</head>
<body>

<!-- Header and hero -->
<header class="hero">
  <div class="hero-art" role="img" aria-label="Isometric illustration of cloud servers, monitor with dashboards, laptop, phone and keyboard"></div>
  <svg class="abs" style="left:0;top:520px" width="1200" height="220" viewBox="0 0 1200 220" aria-hidden="true">
    <path fill="#fff" d="M0 20 C30 0 70 20 80 60 C110 40 150 55 160 90 C200 70 250 85 270 125 C320 110 360 130 380 160 C430 150 480 165 520 180 L640 185 C680 165 740 170 760 185 C800 175 850 170 880 150 C900 150 920 130 940 110 C960 120 980 105 990 125 L1200 160 L1200 220 L0 220 Z"/>
  </svg>
  <div class="brand" style="left:110px;top:32px;color:#fff;font-size:25px">
    <span class="dot" style="width:28px;height:28px;background:#fff"></span>Stratonimbus
  </div>
  <nav class="nav">
    <span>Home</span><span>About Us</span><span>How SNAAS Benefits</span><span>The SNAAS Difference</span><span>Contact Us</span>
  </nav>
  <div class="login">Login</div>
  <h1 class="hero-title display">A groundbreaking way for<br>your small business <b>to benefit<br>from the power of the cloud</b></h1>
  <div class="hero-text">
    Stratonimbus as a Service is here to help small businesses utilise the power of the cloud without complicated set-ups or scary price tags.
    <strong>Ready to modernise your infrastructure with a fully managed<br>private cloud solution from SNaaS?</strong>
  </div>
  <a class="btn btn-white" style="left:110px;top:446px;width:206px;height:44px">CONTACT US <span class="arrow"></span></a>
</header>

<!-- Benefits -->
<section class="benefits">
  <span class="section-mark" style="top:748px"></span>
  <h2 class="section-title display" style="top:768px">How SNAAS benefits <b>your business</b></h2>

  <svg class="abs" style="left:0;top:0" width="1200" height="1200" aria-hidden="true">
    <g stroke="#cfcfcf" stroke-width="1.2" fill="none">
      <path d="M448 889 H500 L545 925"/>
      <path d="M448 1024 H488"/>
      <path d="M448 1156 H500 L545 1122"/>
      <path d="M742 889 H700 L655 925"/>
      <path d="M742 1024 H712"/>
      <path d="M742 1156 H700 L655 1122"/>
    </g>
  </svg>

  <div class="benefit left" style="left:113px;top:853px"><h3>Totally flexible</h3><p>get the cloud you want and the latest innovations you need</p></div>
  <div class="benefit left" style="left:113px;top:987px"><h3>Faster</h3><p>our private cloud solutions outpace public clouds</p></div>
  <div class="benefit left" style="left:113px;top:1116px"><h3>Greater value for money</h3><p>totally transparent pricing for no nasty month-end surprises</p></div>

  <div class="b-icon grey" style="left:368px;top:849px" role="img" aria-label="Flexibility icon"><span></span></div>
  <div class="b-icon grey" style="left:368px;top:984px" role="img" aria-label="Speed icon"><span></span></div>
  <div class="b-icon grey" style="left:368px;top:1116px" role="img" aria-label="Value icon"><span></span></div>

  <div class="hub"><div class="hub-ring"><div class="hub-core"></div></div></div>

  <div class="b-icon blue" style="left:742px;top:849px" role="img" aria-label="Consultancy icon"><span></span></div>
  <div class="b-icon blue" style="left:742px;top:984px" role="img" aria-label="Monitoring icon"><span></span></div>
  <div class="b-icon blue" style="left:742px;top:1116px" role="img" aria-label="Cloud solutions icon"><span></span></div>

  <div class="benefit" style="left:852px;top:853px"><h3>No consultancy fees</h3><p>we'll work with you and charge set fees for everything</p></div>
  <div class="benefit" style="left:852px;top:987px;width:260px"><h3 style="line-height:21px">Management, monitoring and maintenance</h3><p>they're all included in your monthly price</p></div>
  <div class="benefit" style="left:852px;top:1118px;width:260px"><h3>Tried and tested cloud solutions</h3><p>we'll deploy the right OpenStratum solutions for your business</p></div>
</section>

<!-- Digital transformation band -->
<section class="band">
  <span class="section-mark" style="top:42px;background:var(--blue-light)"></span>
  <h2 class="display">SNAAS can drive your digital<br><b>transformation today</b></h2>
  <div class="copy">
    <p>Organisations of all shapes and sizes are reaping the time and money saving benefits that the cloud brings.</p>
    <p>But for small businesses seeking to transition, managing the time and financial costs of transitioning, and knowing whether to opt for a public or private cloud can cause you to hit the pause button.</p>
    <p>SNAAS is here to help you switch on your cloud transformation in a way that works best for you. We deliver and support fully managed private cloud solutions that are:</p>
  </div>
  <div class="trait" style="left:110px"><svg width="104" height="64" viewBox="0 0 104 64" role="img" aria-label="Cloud with stopwatch icon"><path fill="#fff" d="M18 64 C4 64 0 52 6 44 C2 34 12 24 22 28 C26 10 48 4 60 16 C74 6 96 14 94 34 C104 38 104 64 88 64 Z"/><circle cx="50" cy="42" r="11" fill="none" stroke="#1f8ad6" stroke-width="2"/></svg><span style="margin-left:-26px">Fast</span></div>
  <div class="trait" style="left:376px"><svg width="104" height="64" viewBox="0 0 104 64" role="img" aria-label="Cloud with phone icon"><path fill="#fff" d="M18 64 C4 64 0 52 6 44 C2 34 12 24 22 28 C26 10 48 4 60 16 C74 6 96 14 94 34 C104 38 104 64 88 64 Z"/><rect x="44" y="30" width="14" height="24" rx="2" fill="none" stroke="#1f8ad6" stroke-width="2"/></svg><span style="margin-left:-6px">Easy</span></div>
  <div class="trait" style="left:631px"><svg width="104" height="64" viewBox="0 0 104 64" role="img" aria-label="Cloud with scaling icon"><path fill="#fff" d="M18 64 C4 64 0 52 6 44 C2 34 12 24 22 28 C26 10 48 4 60 16 C74 6 96 14 94 34 C104 38 104 64 88 64 Z"/><rect x="40" y="30" width="22" height="20" rx="2" fill="none" stroke="#1f8ad6" stroke-width="2"/></svg><span style="margin-left:-6px">Scalable</span></div>
  <div class="trait" style="left:898px"><svg width="104" height="64" viewBox="0 0 104 64" role="img" aria-label="Cloud with strength icon"><path fill="#fff" d="M18 64 C4 64 0 52 6 44 C2 34 12 24 22 28 C26 10 48 4 60 16 C74 6 96 14 94 34 C104 38 104 64 88 64 Z"/><path d="M44 54 V38 L52 32 L60 38 V54" fill="none" stroke="#1f8ad6" stroke-width="2"/></svg><span style="margin-left:-10px">Powerful</span></div>
  <a class="btn btn-blue" style="left:506px;top:440px;width:187px;height:48px;font-size:16px">GET STARTED</a>
</section>

<!-- Public cloud -->
<section class="public">
  <span class="section-mark" style="top:1908px"></span>
  <h2 class="section-title display" style="top:1928px">If you're using a public <b>cloud now</b>...</h2>

  <article class="card" style="left:110px">
    <div class="c-icon" role="img" aria-label="Handshake icon"></div>
    <h3>You could be paying<br>too much...</h3>
    <p>Public cloud pricing structures have a habit of sneakily scaling up very quickly. With SNAAS, you'll always know what you're paying for your private cloud services.</p>
  </article>
  <article class="card active" style="left:444px">
    <div class="c-icon" role="img" aria-label="Innovation target icon"></div>
    <h3>You're likely not getting the benefits of full functionality...</h3>
    <p>Public cloud providers cannot adopt new innovations and functions as quickly and easily as the private cloud services you'll get from SNAAS.</p>
  </article>
  <article class="card" style="left:777px">
    <div class="c-icon" role="img" aria-label="Cloud database icon"></div>
    <h3>You'll be tied to the services your provider can provide...</h3>
    <p>Public cloud providers will have a limited suite of products and services to offer you. A SNAAS private cloud has no such limitations</p>
  </article>

  <a class="btn btn-blue" style="left:506px;top:2436px;width:187px;height:48px">LET'S TALK <span class="arrow"></span></a>
</section>

<!-- Difference -->
<section class="diff">
  <svg class="diff-art" width="535" height="400" viewBox="0 0 535 400" role="img" aria-label="Photo of a tablet with glowing data streams inside a cloud shape">
    <defs><linearGradient id="diffFill" x1="0" y1="0" x2="1" y2="1"><stop offset="0" stop-color="#0f2c3a"/><stop offset=".55" stop-color="#1d5a73"/><stop offset="1" stop-color="#8a7a6a"/></linearGradient></defs>
    <path fill="url(#diffFill)" d="M70 400 C20 400 0 350 10 300 C0 240 40 190 100 190 C110 110 190 60 260 80 C300 20 400 20 430 90 C500 100 540 160 530 230 C545 300 520 370 460 400 Z"/>
  </svg>
  <span class="abs" style="left:637px;top:70px;width:18px;height:18px;border-radius:50%;background:#fff"></span>
  <h2 class="display">The SNAAS <b>Difference</b></h2>
  <ul>
    <li>We'll quickly get to grips with what your organisation needs, and deliver it via our private cloud solutions.</li>
    <li>Enjoy the ease of the public cloud, combined with the features, innovations and flexibility of the private cloud.</li>
    <li>You can focus on your core business while we support you with a dedicated cloud infrastructure.</li>
    <li>We'll create and deliver the launchpad that will take your business forward.</li>
  </ul>
  <a class="btn btn-white" style="left:637px;top:389px;width:187px;height:48px">LEARN MORE <span class="arrow"></span></a>
</section>

<!-- Contact -->
<section class="contact">
  <span class="section-mark" style="top:3163px"></span>
  <h2 class="section-title display" style="top:3183px">Contact <b>Us</b></h2>

  <div class="contact-info" style="left:195px">
    <svg width="54" height="54" viewBox="0 0 54 54" aria-hidden="true"><path d="M27 6 C18 6 12 13 12 21 C12 32 27 44 27 44 C27 44 42 32 42 21 C42 13 36 6 27 6 Z" fill="none" stroke="#1f8ad6" stroke-width="2.5"/><circle cx="27" cy="21" r="6" fill="none" stroke="#1f8ad6" stroke-width="2.5"/><path d="M6 50 H48" stroke="#1f8ad6" stroke-width="2.5"/></svg>
    <div><h4>LOCATION:</h4><p>Brookvale, Elmstead, Harrowgate</p></div>
  </div>
  <div class="contact-info" style="left:552px">
    <svg width="54" height="54" viewBox="0 0 54 54" aria-hidden="true"><path d="M14 8 L22 16 L17 22 C20 30 25 35 32 38 L38 33 L46 41 L40 48 C24 46 8 30 6 14 Z" fill="none" stroke="#1f8ad6" stroke-width="2.5" stroke-linejoin="round"/></svg>
    <div><h4>PHONE:</h4><p>+1 555 014 2290</p></div>
  </div>
  <div class="contact-info" style="left:812px">
    <svg width="54" height="54" viewBox="0 0 54 54" aria-hidden="true"><rect x="4" y="12" width="46" height="32" fill="none" stroke="#1f8ad6" stroke-width="2.5"/><path d="M4 12 L27 32 L50 12 M4 44 L20 28 M50 44 L34 28" fill="none" stroke="#1f8ad6" stroke-width="2.5"/></svg>
    <div><h4>EMAIL:</h4><p>info@snaas.com</p></div>
  </div>

  <div class="field" style="left:156px;top:3369px;width:431px;height:51px">Name</div>
  <div class="field" style="left:156px;top:3435px;width:431px;height:51px">Email Address</div>
  <div class="field" style="left:156px;top:3501px;width:431px;height:51px">Phone Number</div>
  <div class="field area" style="left:610px;top:3369px;width:434px;height:184px">Message</div>

  <a class="btn btn-blue" style="left:496px;top:3589px;width:206px;height:50px;font-size:16px">SUBMIT NOW <span class="arrow"></span></a>
</section>

<!-- Footer -->
<svg class="abs" style="left:0;top:3720px" width="1200" height="140" viewBox="0 0 1200 140" aria-hidden="true">
  <path fill="#232323" d="M0 60 C30 40 60 60 70 90 C100 40 160 30 190 70 C230 30 300 40 320 80 C360 60 410 70 430 100 C470 80 520 90 540 110 C600 100 650 95 700 105 C740 70 800 70 820 95 C850 60 910 55 940 80 C980 40 1040 50 1060 75 C1100 30 1170 40 1200 70 L1200 140 L0 140 Z"/>
</svg>
<footer class="footer">
  <div class="brand" style="left:110px;top:130px;color:var(--blue);font-size:25px">
    <span class="dot" style="width:28px;height:28px;background:var(--blue)"></span>Stratonimbus
  </div>

  <div class="f-col" style="left:382px">
    <h4>Our Office Address</h4>
    <div class="f-contact"><i></i><b>Phone</b>+1 555 014 2290</div>
    <div class="f-contact"><i></i><b>Email</b>info@snaas.com</div>
    <div class="f-contact"><i></i><b>Location</b>R. Harbour Lane, 14, Store D,<br>8600-210</div>
  </div>

  <div class="f-col f-links" style="left:620px">
    <h4>Company</h4>
    <a>Home</a><a>About Us</a><a>How SNAAS Benefits</a><a>The SNAAS Difference</a><a>Contact Us</a>
  </div>

  <div class="f-col" style="left:787px"><h4 style="font-size:17px">Subscribe for Updates</h4></div>
  <div class="subscribe"><span>Email Address</span><em>SUBMIT</em></div>
  <div class="abs" style="left:790px;top:162px;font-size:12.5px;font-weight:500;display:flex;align-items:center;gap:10px">
    <span style="width:11px;height:11px;border:1.5px solid #e8e8e8;border-radius:2px"></span>Yes, Please Contact me.
  </div>
  <span class="social" style="left:787px" role="img" aria-label="Social profile link"></span>
  <span class="social" style="left:829px" role="img" aria-label="Social profile link"></span>
  <span class="social" style="left:871px" role="img" aria-label="Social profile link"></span>

  <div class="abs" style="left:1010px;top:252px;width:78px;height:22px;border-radius:11px;background:#2e2e2e;font-size:11px;font-weight:700;display:flex;align-items:center;justify-content:center">&#8593; Go Up</div>
  <div class="abs" style="left:110px;top:272px;width:978px;height:1px;background:#3a3a3a"></div>

  <div class="legal" style="left:110px">© 2022 SNAAS | All Rights Reserved</div>
  <div class="legal" style="left:760px">Privacy Policy &nbsp;|&nbsp; Cookie Policy &nbsp;|&nbsp; Terms Of Services</div>
</footer>

</body>
</html>
```